4th Generation Family Business Needs a New Card Design!

We are a family owned 4th Generation company. We are based in the Sydney, Australia area and we are desperately in need of a more modern and classy card. We are monumental masons who design, supply & erect lasting memorials throughout cemeteries in Sydney. Our customers are normally in a period of grieving. I have attached logo files that will need to be implemented on the card. Company was established 1935. Australian Owned and Operated. Card needs to be designed to PIXO.com specification.

Target Market(s)

Our target market is based upon people that a grieving for family members that have passed away. We also deal with alot of companies that own and operate cemeteries.

Industry/Entity Type

Business

Contact Information for Business Card

Simon Harcourt, Operations Manager, 0417293086, simon@harcourtmemorials.com.au
Lewis Harcourt, Director, 0491630572, lewis@harcourtmemorials.com.au
Phone # 02 9561 3048
Website: www.harcourtmemorials.com.au
Address: Suite 17, 8 Palfrey Lane, West Carlow, Sydney NSW 2156

Font styles to use
Serif
Decorative
Script

Requirements
Must have
• Would like to see the logo nicely implemented with a modern design. Embossed lettering would be a nice additive.

```html
<!DOCTYPE html>
<html lang="en">
<head>
<meta charset="utf-8">
<title>Harcourt Memorials — Business Card</title>
<link rel="stylesheet" href="https://fonts.googleapis.com/css2?family=Open+Sans:wght@400;600;700&display=swap">
<style>
  :root {
    --page: #e9e6e1;
    --card: #f4f2ee;
    --card-edge: #dcd8d1;
    --ink: #1c1c1c;
    --ink-soft: #2e2e2e;
    --gold: #e5b72a;
  }
  * { margin: 0; padding: 0; box-sizing: border-box; }
  html, body {
    width: 909px;
    height: 1200px;
    overflow: hidden;
    background: var(--page);
    font-family: "Open Sans", Arial, sans-serif;
    color: var(--ink);
  }
  .canvas {
    position: relative;
    width: 909px;
    height: 1200px;
  }
  .card {
    position: absolute;
    left: 105px;
    width: 700px;
    height: 428px;
    background: var(--card);
    border: 1px solid var(--card-edge);
    box-shadow: 0 6px 18px rgba(0,0,0,0.12);
  }
  .card--front { top: 110px; }
  .card--back  { top: 662px; }

  .brand {
    position: absolute;
    display: flex;
    align-items: center;
    gap: 12px;
    white-space: nowrap;
  }
  .brand__mark {
    flex: none;
    background: var(--gold);
  }
  .brand__name {
    font-weight: 700;
    color: var(--ink);
    text-transform: uppercase;
    letter-spacing: 0.08em;
    line-height: 1;
  }
  .card--front .brand { right: 46px; bottom: 56px; }
  .card--front .brand__mark { width: 16px; height: 16px; }
  .card--front .brand__name { font-size: 18px; }

  .card--back .brand { right: 52px; bottom: 52px; }
  .card--back .brand__mark { width: 20px; height: 20px; }
  .card--back .brand__name { font-size: 23px; }

  .contact {
    position: absolute;
    left: 372px;
    top: 52px;
    width: 300px;
  }
  .contact__name {
    font-size: 22px;
    font-weight: 700;
    letter-spacing: 0.01em;
    line-height: 1.1;
  }
  .contact__role {
    font-size: 16px;
    font-weight: 600;
    line-height: 1.25;
    margin-bottom: 10px;
  }
  .contact__line {
    font-size: 13px;
    line-height: 1.45;
    color: var(--ink-soft);
  }
  .contact__line b { font-weight: 700; }
  .contact__address { margin-top: 8px; }
  .contact__rule {
    width: 86px;
    height: 2px;
    background: var(--ink);
    margin-top: 12px;
  }
</style>
</head>
<body>
<main class="canvas">
  <section class="card card--front" aria-label="Card front">
    <div class="brand">
      <span class="brand__mark" aria-hidden="true"></span>
      <span class="brand__name">Harcourt Memorials</span>
    </div>
  </section>

  <section class="card card--back" aria-label="Card back">
    <div class="contact">
      <h1 class="contact__name">SIMON HARCOURT</h1>
      <p class="contact__role">Operations Manager</p>
      <p class="contact__line"><b>M.</b> 0417293086 <b>P.</b> 02 9561 3048</p>
      <p class="contact__line">simon@harcourtmemorials.com.au</p>
      <p class="contact__line">www.harcourtmemorials.com.au</p>
      <p class="contact__line contact__address">Suite 17, 8 Palfrey Lane<br>West Carlow, Sydney NSW 2156</p>
      <div class="contact__rule"></div>
    </div>
    <div class="brand">
      <span class="brand__mark" aria-hidden="true"></span>
      <span class="brand__name">Harcourt Memorials</span>
    </div>
  </section>
</main>
</body>
</html>
```